a business advisory consulting website

I need a website 3-5 pages to sell my professional services in IT and Project management Consulting. My company name is Crestline Advisory Consulting. I want it to be device friendly and easy to navigate for the busy executive however intriguing enough.
I have attached some info I drafted on About the company and personal Bio. Also there is a website that I really like that I have attached the initial site pdf and websites that I like are here: https://tollmeradvisors.example, https://quarvelanalytics.example, https://www.dorvikstudylearning.example as examples. Thanks
Updates

Hi Designers, I have uploaded the logo in 3D .png format, to assist in the web design.

Target Market(s)

B2B, governments, IT companies, Project Management companies and Consulting firms, small medium enterprises to large corporate enterprises.

Industry/Entity Type

It Professional

Coding

Coded - Design and coding required

Number of Pages Required

5+ page

Font styles to use
Sans Serif

Requirements
Must have
• Home, About company, the team, what we do and contact us
Nice to have
• Blog
Should not have
• pop ups, flash

```html
<!DOCTYPE html>
<html lang="en">
<head>
<meta charset="utf-8">
<title>Crestline Advisory Consulting</title>
<link href="https://fonts.googleapis.com/css2?family=Oswald:wght@400;500;600&family=Roboto:ital,wght@0,400;0,500;0,700;1,400&display=swap" rel="stylesheet">
<style>
:root{
  --red:#e3262d;
  --navy:#1f2a44;
  --ink:#2b2b2b;
  --text:#4a4a4a;
  --pink:#fbe1e2;
  --lavender:#dde0f5;
  --footer:#7d1c26;
  --line:#d9d9d9;
}
*{margin:0;padding:0;box-sizing:border-box}
html,body{width:1200px;height:5186px;overflow:hidden;background:#fff}
body{position:relative;font-family:"Roboto",sans-serif;color:var(--text)}
.abs{position:absolute}
.heading{font-family:"Oswald",sans-serif;color:var(--ink);font-weight:500;text-transform:uppercase}
.btn-outline{position:absolute;border:2px solid var(--red);border-radius:24px;color:var(--red);font:700 15px "Roboto",sans-serif;display:flex;align-items:center;justify-content:center;text-transform:uppercase;background:#fff}
.body-copy{font-size:13px;line-height:28px;color:#444}
.photo{position:absolute}
.vtitle{position:absolute;writing-mode:vertical-rl;font-family:"Oswald",sans-serif;color:var(--ink);text-transform:uppercase;white-space:nowrap}
.card{position:absolute;background:#fff;box-shadow:0 4px 18px rgba(0,0,0,.16)}

/* hero */
.hero{position:absolute;left:0;top:0;width:1200px;height:557px;background:linear-gradient(120deg,#6d6a68 0%,#b3aca5 40%,#d9d4cf 70%,#8d8580 100%)}
.topbar{position:absolute;left:0;top:0;width:1200px;height:95px;background:rgba(255,255,255,.82)}
.logo{position:absolute;left:112px;top:36px;display:flex;align-items:center;gap:10px;font:700 17px "Roboto",sans-serif;color:var(--navy);text-transform:uppercase;line-height:1;white-space:nowrap}
.logo i{width:22px;height:22px;background:var(--red);display:block}
.nav{position:absolute;left:330px;top:38px;display:flex;gap:30px;font-size:15px;color:#333;white-space:nowrap}
.nav .active{color:var(--red);border-bottom:2px solid var(--red);padding-bottom:8px}
.talk{left:860px;top:28px;width:227px;height:44px;font-size:14px;background:transparent}
.hero-line{position:absolute;left:140px;font-family:"Oswald",sans-serif;font-weight:500;font-size:40px;text-transform:uppercase;padding:0 12px;line-height:60px;white-space:nowrap}
.l1{top:205px;background:var(--lavender);color:var(--navy)}
.l2{top:272px;background:var(--red);color:#fff;line-height:80px;padding:0 14px}
.l3{top:360px;background:var(--lavender);color:var(--navy)}
.getstarted{position:absolute;left:143px;top:456px;width:185px;height:44px;border-radius:22px;background:var(--navy);color:#fff;font:700 14px "Roboto",sans-serif;display:flex;align-items:center;justify-content:center}
.dots{position:absolute;left:556px;top:524px;display:flex;gap:10px}
.dots span{width:12px;height:12px;border-radius:50%;background:#f0a5a8}
.dots .on{background:var(--red);width:16px;height:16px;margin-top:-2px}

/* footer */
.footer{position:absolute;left:0;top:4838px;width:1200px;height:348px;background:var(--footer);color:#fff}
.footer .logo{left:135px;top:92px;color:#fff;font-size:26px}
.footer .logo i{width:30px;height:30px;background:#fff}
.fnav{position:absolute;left:587px;top:104px;display:flex;gap:24px;font-size:15px;white-space:nowrap}
.ftext{position:absolute;left:135px;top:170px;width:330px;font:500 14px/28px "Roboto",sans-serif}
.social{position:absolute;top:188px;width:36px;height:36px;border-radius:50%;background:#fff}
.fline{position:absolute;left:112px;top:270px;width:976px;height:1px;background:rgba(255,255,255,.5)}
.copy{position:absolute;left:0;top:296px;width:1200px;text-align:center;font-size:13px}

.field{position:absolute;border-bottom:1px solid var(--line);font-size:12px;color:#777;text-transform:uppercase;padding-bottom:10px}
.quote-name{position:absolute;top:4047px;font:700 20px "Roboto",sans-serif;color:var(--red)}
.quote-text{position:absolute;top:4090px;width:265px;font:italic 14px/28px "Roboto",sans-serif;color:#555}
.quote-mark{position:absolute;top:4190px;font:700 110px/110px "Oswald",sans-serif;color:var(--ink)}
</style>
</head>
<body>

<!-- Hero -->
<header>
  <div class="hero" role="img" aria-label="Photo of a diverse business team meeting around a table with laptops"></div>
  <div class="topbar"></div>
  <div class="logo"><i></i>Crestline Advisory</div>
  <nav class="nav">
    <span class="active">Home</span><span>About company</span><span>The team</span><span>What we do</span><span>Contact us</span>
  </nav>
  <div class="btn-outline talk">Talk to a representative</div>
  <div class="hero-line l1">We will bring</div>
  <div class="hero-line l2">Your&nbsp; business product ideas</div>
  <div class="hero-line l3">To reality</div>
  <div class="getstarted">GET STARTED</div>
  <div class="dots"><span></span><span class="on"></span><span></span><span></span></div>
</header>

<!-- About -->
<section>
  <div class="abs" style="left:125px;top:660px;width:393px;height:478px;border:7px solid var(--red)"></div>
  <div class="photo" style="left:135px;top:646px;width:388px;height:484px;background:linear-gradient(160deg,#2c3f6b,#8a6a4e 55%,#c9c3ba)" role="img" aria-label="Photo of a team collaborating around a desk under pendant lights"></div>
  <div class="abs body-copy" style="left:588px;top:680px;width:378px">
    <p>We are a specialist operational excellence firm, delivering consulting and advisory services in six core capabilities, across all industries and all business lines to improve performance, efficiency, profitability, automation and scalability, for clients across Australia.</p>
    <p style="margin-top:12px">We’re known for our pragmatism, in depth analysis, strategic insight and nurturing long-term client self-sufficiency. We approach business consulting differently, with a Genuine Client Partnership model that builds client capability and rightsized solutions for the client.</p>
  </div>
  <div class="btn-outline" style="left:588px;top:1050px;width:184px;height:45px">Know more</div>
  <div class="vtitle" style="left:1018px;top:680px;font-size:44px;font-weight:600;line-height:50px">About</div>
  <div class="vtitle" style="left:996px;top:690px;font-size:14px;line-height:18px">Crestline advisory</div>
  <div class="abs" style="left:1000px;top:838px;width:14px;height:202px;background:var(--red)"></div>
</section>

<!-- Services -->
<section>
  <svg class="abs" style="left:0;top:1260px" width="1200" height="218" viewBox="0 0 1200 218" aria-hidden="true">
    <path d="M0 160 C80 70 150 60 230 100 C330 150 380 200 470 170 C560 140 620 60 720 80 C820 100 850 180 960 150 C1060 120 1130 60 1200 0 L1200 218 L0 218 Z" fill="var(--pink)"/>
  </svg>
  <div class="heading abs" style="left:480px;top:1200px;font-size:36px;line-height:90px;white-space:nowrap"><span style="font-size:86px;font-weight:600;vertical-align:-8px">O</span>ur services</div>
  <div class="abs" style="left:510px;top:1305px;width:1px;height:65px;background:#999"></div>
  <div class="vtitle" style="left:490px;top:1380px;font-size:30px;font-weight:600;line-height:30px">What we do</div>
</section>

<!-- Process improvement -->
<section>
  <h2 class="heading abs" style="left:208px;top:1660px;font-size:33px;line-height:42px">Process improvement within<br>government</h2>
  <div class="abs" style="left:657px;top:1715px;width:1px;height:130px;background:var(--red)"></div>
  <div class="card" style="left:0;top:1865px;width:712px;height:270px"></div>
  <p class="abs body-copy" style="left:211px;top:1910px;width:452px;text-align:justify">Across the three levels of Government – Federal, State/Territory and Local – leaders continually face complex decisions around how to allocate limited resources to best service their citizens.&nbsp; In the past, Governments have faced criticism</p>
  <div class="btn-outline" style="left:211px;top:2045px;width:182px;height:45px">Know more</div>
  <div class="photo" style="left:750px;top:1614px;width:330px;height:436px;background:linear-gradient(170deg,#dcdfe4,#8a8f96 50%,#5a4a3c)" role="img" aria-label="Photo of colleagues reviewing documents at a wooden table"></div>
</section>

<!-- Technology analysis -->
<section>
  <div class="photo" style="left:118px;top:2224px;width:332px;height:436px;background:linear-gradient(135deg,#c8d6e3,#6f8aa3 55%,#2c3a4c)" role="img" aria-label="Photo of a medical professional analysing scans on computer monitors"></div>
  <h2 class="heading abs" style="left:520px;top:2250px;font-size:33px;line-height:42px">Technology analysis within<br>healthcare</h2>
  <div class="abs" style="left:541px;top:2345px;width:1px;height:110px;background:var(--red)"></div>
  <div class="card" style="left:487px;top:2475px;width:740px;height:270px"></div>
  <p class="abs body-copy" style="left:535px;top:2522px;width:460px">Australia’s health care system is a complex web of public and private providers, settings, participants and supporting mechanisms. Health providers include medical practitioners, nurses, allied and other health professionals, hospitals, clinics and government agencies</p>
  <div class="btn-outline" style="left:535px;top:2652px;width:184px;height:45px">Know more</div>
</section>

<!-- Team -->
<section>
  <div class="vtitle" style="left:110px;top:2855px;font-size:42px;font-weight:600;line-height:46px;transform:rotate(180deg)">The team</div>
  <div class="vtitle" style="left:160px;top:2880px;font-size:14px;line-height:18px;transform:rotate(180deg)">Marcus Adeyemi</div>
  <div class="abs" style="left:166px;top:3035px;width:12px;height:205px;background:var(--red)"></div>
  <h3 class="abs" style="left:250px;top:2852px;font:500 24px 'Roboto',sans-serif;color:var(--red)">Marcus Adeyemi</h3>
  <div class="abs body-copy" style="left:252px;top:2900px;width:378px;font-size:12.5px">
    <p>Marcus Adeyemi is an IT professional with more than 20 years of experience turning business initiatives into technology solutions. His expertise has been identifying deficiencies and developing or facilitating the best solutions for an outcome that is satisfactory to all stakeholders involved.</p>
    <p style="margin-top:12px">Marcus improves business processes as older organizations restructure or migrate to newer technologies. He bridges the gap between the actual people in these organizations transitioning and the new technologies they seek which is a value add to any organization’s success.</p>
  </div>
  <div class="btn-outline" style="left:254px;top:3250px;width:183px;height:45px">Know more</div>
  <div class="abs" style="left:795px;top:2817px;width:405px;height:535px;background:var(--pink)"></div>
  <div class="photo" style="left:683px;top:2853px;width:388px;height:469px;background:linear-gradient(160deg,#9fb3a8,#56646a 50%,#1f2f5a)" role="img" aria-label="Portrait photo of a consultant in a blue suit"></div>
</section>

<!-- Reviews -->
<section>
  <svg class="abs" style="left:460px;top:3450px" width="280" height="280" viewBox="0 0 280 280" aria-hidden="true">
    <circle cx="140" cy="140" r="136" fill="none" stroke="#eee" stroke-width="2"/>
    <circle cx="140" cy="140" r="118" fill="none" stroke="#f3f3f3" stroke-width="1"/>
  </svg>
  <div class="heading abs" style="left:528px;top:3535px;font-size:36px;line-height:90px;white-space:nowrap"><span style="font-size:86px;font-weight:600;vertical-align:-8px">R</span>eview</div>
  <div class="abs" style="left:553px;top:3640px;width:1px;height:110px;background:var(--red)"></div>
  <div class="vtitle" style="left:530px;top:3755px;font-size:36px;font-weight:600;line-height:38px">By our</div>
  <div class="vtitle" style="left:505px;top:3820px;font-size:20px;font-weight:500;line-height:24px">clients</div>

  <svg class="abs" style="left:50px;top:4091px" width="32" height="32" viewBox="0 0 32 32" aria-hidden="true"><circle cx="16" cy="16" r="14" fill="none" stroke="var(--red)" stroke-width="1.5"/><path d="M22 16H10M15 11l-5 5 5 5" fill="none" stroke="var(--red)" stroke-width="1.5"/></svg>
  <svg class="abs" style="left:1107px;top:4091px" width="32" height="32" viewBox="0 0 32 32" aria-hidden="true"><circle cx="16" cy="16" r="14" fill="none" stroke="var(--red)" stroke-width="1.5"/><path d="M10 16h12M17 11l5 5-5 5" fill="none" stroke="var(--red)" stroke-width="1.5"/></svg>

  <div class="card" style="left:112px;top:3980px;width:305px;height:282px"></div>
  <div class="card" style="left:447px;top:3980px;width:305px;height:282px"></div>
  <div class="card" style="left:783px;top:3980px;width:305px;height:282px"></div>

  <div class="abs" style="left:128px;top:3942px;width:80px;height:80px;border-radius:50%;background:linear-gradient(#7a8ba0,#3a4250)" role="img" aria-label="Client portrait photo"></div>
  <div class="abs" style="left:463px;top:3942px;width:80px;height:80px;border-radius:50%;background:linear-gradient(#c9ccd1,#2d2d2d)" role="img" aria-label="Client portrait photo"></div>
  <div class="abs" style="left:799px;top:3942px;width:80px;height:80px;border-radius:50%;background:linear-gradient(#d8d2c6,#6b5a48)" role="img" aria-label="Client portrait photo"></div>

  <h4 class="quote-name" style="left:132px">JORDAN ELLIS</h4>
  <h4 class="quote-name" style="left:467px">JORDAN ELLIS</h4>
  <h4 class="quote-name" style="left:803px">JORDAN ELLIS</h4>

  <p class="quote-text" style="left:132px">Lorem ipsum dolor t , consectetur adipiscing elit, sed do eiusmod tempor incididunt ut labore et dolore magna aliqua.</p>
  <p class="quote-text" style="left:467px">Lorem ipsum dolor t , consectetur adipiscing elit, sed do eiusmod tempor incididunt ut labore et dolore magna aliqua.</p>
  <p class="quote-text" style="left:803px">Lorem ipsum dolor t , consectetur adipiscing elit, sed do eiusmod tempor incididunt ut labore et dolore magna aliqua.</p>

  <div class="quote-mark" style="left:338px">”</div>
  <div class="quote-mark" style="left:673px">”</div>
  <div class="quote-mark" style="left:1009px">”</div>

  <div class="abs" style="left:958px;top:4290px;width:45px;height:3px;background:var(--red)"></div>
  <div class="abs" style="left:1013px;top:4290px;width:32px;height:3px;background:#999"></div>
  <div class="abs" style="left:1055px;top:4290px;width:32px;height:3px;background:#999"></div>
</section>

<!-- Contact -->
<section>
  <div class="card" style="left:110px;top:4460px;width:457px;height:327px"></div>
  <div class="field" style="left:140px;top:4500px;width:188px">Name</div>
  <div class="field" style="left:346px;top:4500px;width:190px">Last name</div>
  <div class="field" style="left:140px;top:4552px;width:396px">Email</div>
  <div class="field" style="left:140px;top:4625px;width:396px">Message</div>
  <div class="btn-outline" style="left:244px;top:4668px;width:182px;height:44px">Know more</div>

  <svg class="abs" style="left:640px;top:4515px" width="34" height="40" viewBox="0 0 34 40" aria-hidden="true"><path d="M17 2C9 2 3 8 3 15c0 10 14 23 14 23s14-13 14-23C31 8 25 2 17 2z" fill="var(--red)"/><circle cx="17" cy="15" r="5" fill="#fff"/></svg>
  <p class="abs" style="left:692px;top:4508px;font-size:15px;line-height:27px;color:#555">48 Harbor Lane, Fairview<br>10150, United States</p>
  <svg class="abs" style="left:640px;top:4596px" width="34" height="34" viewBox="0 0 34 34" aria-hidden="true"><circle cx="17" cy="17" r="15" fill="none" stroke="var(--red)" stroke-width="2"/><path d="M11 9l4 0 2 5-3 2c1 3 3 5 6 6l2-3 5 2v4c-9 1-17-7-16-16z" fill="var(--red)"/></svg>
  <p class="abs" style="left:692px;top:4603px;font-size:15px;color:#555">(555) 014-2290</p>
  <svg class="abs" style="left:640px;top:4670px" width="34" height="26" viewBox="0 0 34 26" aria-hidden="true"><rect x="2" y="2" width="30" height="22" fill="var(--red)"/><path d="M2 3l15 12L32 3" fill="none" stroke="#fff" stroke-width="2"/></svg>
  <p class="abs" style="left:692px;top:4673px;font-size:15px;color:#555">info@crestlineadvisory.example</p>

  <div class="vtitle" style="left:1018px;top:4365px;font-size:44px;font-weight:600;line-height:50px">Contact</div>
  <div class="vtitle" style="left:996px;top:4375px;font-size:14px;line-height:18px">Crestline advisory</div>
  <div class="abs" style="left:1000px;top:4520px;width:14px;height:220px;background:var(--red)"></div>
</section>

<!-- Footer -->
<footer class="footer">
  <div class="logo"><i></i>Crestline Advisory</div>
  <nav class="fnav"><span>Home</span><span>About company</span><span>The team</span><span>What we do</span><span>Contact us</span></nav>
  <p class="ftext">Lorem ipsum dolor sit amet, consectetur adipiscing elit, sed do eiusmod tempor incididunt ut labore et dolore magna aliqua.</p>
  <span class="social" style="left:760px"></span>
  <span class="social" style="left:812px"></span>
  <span class="social" style="left:865px"></span>
  <div class="fline"></div>
  <p class="copy">Copyright © 2020 Crestline Advisory. All Rights Reserved.</p>
</footer>

</body>
</html>
```